Brightmoor Essentials colloidal silver spray for pets.

We need a label for an 8-oz cobalt blue spray bottle. We are a small company just starting to share the benefits of colloidal silver. Our first offering will be the 8-oz spray bottle for pets. We would also like to update our logo. The finished project should be crisp and incorporate a dog on the label. I have attached the information we would like on the label and our logo, which can be changed to match your vision.
Updates

Hi, I would like to remind you that we are using a cobalt blue bottle with a black sprayer and would like an updated logo. Also, for the business cards, we don't want an animal on them, as we are planning future products for people. thank you

```html
<!DOCTYPE html>
<html lang="en">
<head>
<meta charset="utf-8">
<title>Brightmoor Essentials – Colloidal Silver Label</title>
<link rel="stylesheet" href="https://fonts.googleapis.com/css2?family=Baloo+2:wght@600;700;800&family=Sancreek&display=swap">
<style>
  :root {
    --bg: #ececec;
    --label-top: #e3e6f4;
    --label-mid: #8f9bd0;
    --label-bottom: #3d56a8;
    --title-green: #159a4c;
    --title-outline: #0b5b2c;
    --band: #2b3190;
    --white: #ffffff;
    --dim-blue: #2a6fb0;
    --brand-blue: #1d47b8;
    --art-light: #f2d3b4;
    --art-mid: #e7a77a;
  }
  * { margin: 0; padding: 0; box-sizing: border-box; }
  html, body { width: 1200px; height: 1200px; overflow: hidden; }
  body {
    background: radial-gradient(circle at 50% 50%, #fafafa 0%, var(--bg) 70%, #dcdcdc 100%);
    font-family: "Baloo 2", sans-serif;
    position: relative;
  }
  .brand-lockup {
    position: absolute;
    top: 60px; left: 0; width: 1200px;
    display: flex; align-items: center; justify-content: center; gap: 18px;
  }
  .brand-lockup .dot {
    width: 34px; height: 34px; border-radius: 50%;
    background: var(--brand-blue);
  }
  .brand-lockup .name {
    font-size: 58px; font-weight: 700; color: var(--brand-blue);
    letter-spacing: 1px;
  }
  .dimension { position: absolute; }
  .dimension-width { top: 190px; left: 395px; width: 410px; height: 40px; }
  .dimension-height { top: 260px; left: 330px; width: 40px; height: 860px; }
  .dimension-label {
    position: absolute; font-family: Arial, Helvetica, sans-serif;
    font-size: 26px; color: var(--dim-blue); background: transparent;
  }
  .dimension-width .dimension-label { top: 2px; left: 0; width: 410px; text-align: center; }
  .dimension-height .dimension-label {
    top: 415px; left: -50px; width: 140px; text-align: center;
    transform: rotate(-90deg);
  }
  .label {
    position: absolute; top: 260px; left: 395px;
    width: 410px; height: 860px;
    background: linear-gradient(180deg, var(--label-top) 0%, var(--label-mid) 45%, var(--label-bottom) 100%);
    display: flex; flex-direction: column; align-items: center;
    color: var(--white);
  }
  .label-brand {
    margin-top: 34px;
    display: flex; align-items: center; gap: 8px;
  }
  .label-brand .dot { width: 12px; height: 12px; border-radius: 50%; background: var(--brand-blue); }
  .label-brand .name { font-size: 21px; font-weight: 700; color: var(--brand-blue); }
  .product-title {
    margin-top: 28px;
    font-family: "Sancreek", serif;
    color: var(--title-green);
    text-align: center; line-height: 0.95;
    -webkit-text-stroke: 1px var(--title-outline);
  }
  .product-title .line-1 { display: block; font-size: 70px; letter-spacing: 0; }
  .product-title .line-2 { display: block; font-size: 76px; }
  .tagline-band {
    margin-top: 16px;
    background: var(--band); border-radius: 14px;
    width: 330px; padding: 6px 0 4px;
    text-align: center; font-weight: 800; font-size: 25px; line-height: 1.2;
    letter-spacing: 0.5px;
  }
  .spec-list {
    margin-top: 12px; text-align: center;
    font-weight: 700; font-size: 18px; line-height: 1.15;
  }
  .spec-list .rule { width: 230px; height: 2px; background: var(--white); margin: 5px auto 6px; }
  .benefits {
    text-align: center; font-weight: 700; font-size: 15.5px; line-height: 1.15;
  }
  .art-area {
    position: relative;
    margin-top: 14px; width: 340px; height: 330px;
    border-radius: 40px 40px 20px 20px;
    background: radial-gradient(ellipse at 55% 45%, var(--art-light) 0%, var(--art-mid) 70%, rgba(231,167,122,0.2) 100%);
  }
  .origin-badge {
    position: absolute; top: 110px; right: -28px;
    width: 62px; height: 62px; border-radius: 50%;
    background: var(--white); border: 3px solid #d8d8d8;
  }
  .volume {
    margin-top: auto; margin-bottom: 22px;
    font-weight: 700; font-size: 18px;
  }
</style>
</head>
<body>
  <header class="brand-lockup">
    <span class="dot"></span>
    <span class="name">Brightmoor Essentials</span>
  </header>

  <div class="dimension dimension-width">
    <svg width="410" height="40" viewBox="0 0 410 40">
      <line x1="1" y1="4" x2="1" y2="36" stroke="#2a6fb0" stroke-width="1.5"/>
      <line x1="409" y1="4" x2="409" y2="36" stroke="#2a6fb0" stroke-width="1.5"/>
      <line x1="2" y1="20" x2="125" y2="20" stroke="#2a6fb0" stroke-width="1.5"/>
      <line x1="285" y1="20" x2="408" y2="20" stroke="#2a6fb0" stroke-width="1.5"/>
      <polygon points="2,20 22,14 22,26" fill="#2a6fb0"/>
      <polygon points="408,20 388,14 388,26" fill="#2a6fb0"/>
    </svg>
    <span class="dimension-label">6.20 cm</span>
  </div>

  <div class="dimension dimension-height">
    <svg width="40" height="860" viewBox="0 0 40 860">
      <line x1="2" y1="1" x2="38" y2="1" stroke="#2a6fb0" stroke-width="1.5"/>
      <line x1="2" y1="859" x2="38" y2="859" stroke="#2a6fb0" stroke-width="1.5"/>
      <line x1="20" y1="2" x2="20" y2="360" stroke="#2a6fb0" stroke-width="1.5"/>
      <line x1="20" y1="500" x2="20" y2="858" stroke="#2a6fb0" stroke-width="1.5"/>
      <polygon points="20,2 14,22 26,22" fill="#2a6fb0"/>
      <polygon points="20,858 14,838 26,838" fill="#2a6fb0"/>
    </svg>
    <span class="dimension-label">13.00 cm</span>
  </div>

  <main class="label">
    <div class="label-brand">
      <span class="dot"></span>
      <span class="name">Brightmoor Essentials</span>
    </div>

    <h1 class="product-title">
      <span class="line-1">COLLOIDAL</span>
      <span class="line-2">SILVER</span>
    </h1>

    <div class="tagline-band">NATURAL FIRST AID<br>FOR PETS</div>

    <div class="spec-list">
      <p>10 PPM - No Preservaties</p>
      <p>100% Pure - No Additives</p>
      <div class="rule"></div>
    </div>

    <div class="benefits">
      <p>Anti microbial, Anti Fungal,</p>
      <p>Anti Bacterial, Anti Viral</p>
      <p>Treats burns, Bites, Cuts, Abrasions,</p>
      <p>Hots Spots</p>
    </div>

    <div class="art-area" role="img" aria-label="Illustration of a beagle puppy and a ginger cat sitting together with a small heart">
      <span class="origin-badge" role="img" aria-label="Origin badge"></span>
    </div>

    <p class="volume">8 oz / 250 ml</p>
  </main>
</body>
</html>
```